I am hosting a banquet called, Copper & Pearl Gala and I need a design to help sell it on Linkora.

Hi all.
No disco balls, please.
I would like a miser-traditional design, classy.

```html
<!DOCTYPE html>
<html lang="en">
<head>
<meta charset="utf-8">
<title>Copper &amp; Pearl Gala – Invitation</title>
<link rel="stylesheet" href="https://fonts.googleapis.com/css2?family=Cormorant:wght@600&family=Marcellus&family=Playfair+Display:wght@500&family=Poppins:wght@400;500;600;700&display=swap">
<style>
  :root {
    --page: #ffffff;
    --card: #0b0b0b;
    --ink: #f3f0e8;
    --silver-hi: #f4f4f4;
    --silver-lo: #8c8c8c;
    --frame: #b9b9b9;
    --band-mid: #9a9a9a;
    --band-edge: #161616;
  }
  * { margin: 0; padding: 0; box-sizing: border-box; }
  html, body { width: 1200px; height: 1200px; overflow: hidden; background: var(--page); }
  .canvas { position: relative; width: 1200px; height: 1200px; }
  .invitation {
    position: absolute; left: 150px; top: 150px; width: 908px; height: 908px;
    background: var(--card); overflow: hidden; color: var(--ink);
    font-family: "Poppins", sans-serif;
  }
  .invitation > * { position: absolute; }
  .ornament-field {
    left: 120px; top: 60px; width: 668px; height: 800px; border-radius: 50%;
    background: radial-gradient(ellipse at center, rgba(70,70,70,.35) 0%, rgba(40,40,40,.2) 45%, rgba(11,11,11,0) 72%);
  }
  .frame-art, .panel-art { left: 0; top: 0; width: 908px; height: 908px; }
  .medallion {
    width: 40px; height: 40px; border-radius: 50%;
    background: radial-gradient(circle, #d8d8d8 0%, #7a7a7a 70%, #3a3a3a 100%);
  }
  .medallion.top { left: 433px; top: 11px; }
  .medallion.bottom { left: 433px; top: 855px; }
  .medallion.left { left: 11px; top: 434px; }
  .medallion.right { left: 855px; top: 434px; }
  .centered { left: 0; width: 908px; text-align: center; }
  .host {
    top: 148px; font-family: "Cormorant", serif; font-weight: 600;
    font-size: 33px; letter-spacing: .5px;
  }
  .event-title {
    top: 192px; font-family: "Playfair Display", serif; font-weight: 500;
    font-size: 58px; line-height: 1.2;
    background: linear-gradient(180deg, var(--silver-hi) 0%, #cfcfcf 45%, var(--silver-lo) 100%);
    -webkit-background-clip: text; background-clip: text; color: transparent;
  }
  .title-flourish {
    left: 372px; top: 300px; width: 172px; height: 26px; border-radius: 13px;
    background: linear-gradient(90deg, rgba(180,180,180,0), rgba(200,200,200,.7) 50%, rgba(180,180,180,0));
  }
  .invite-line {
    left: 288px; top: 374px; width: 356px; height: 25px;
    border-top: 1px solid var(--frame); border-bottom: 1px solid var(--frame);
    font-size: 12.5px; font-weight: 700; letter-spacing: 4.6px;
    text-align: center; line-height: 23px; padding-left: 4px;
  }
  .event-date { top: 418px; font-family: "Marcellus", serif; font-size: 45px; }
  .schedule-band {
    left: 0; top: 506px; width: 908px; height: 80px;
    background: linear-gradient(90deg, var(--band-edge) 0%, #3c3c3c 18%, var(--band-mid) 50%, #3c3c3c 82%, var(--band-edge) 100%);
  }
  .schedule-band .slot {
    position: absolute; top: 0; height: 80px; display: flex; flex-direction: column;
    justify-content: center; align-items: center; font-size: 20px; line-height: 1.25;
  }
  .slot.social { left: 232px; width: 0; }
  .slot.social span, .slot.dinner span { white-space: nowrap; }
  .slot.day { left: 322px; width: 249px; font-size: 31px; font-weight: 500;
    border-left: 1px solid #7a7a7a; border-right: 1px solid #7a7a7a; }
  .slot.dinner { left: 656px; width: 0; }
  .venue { top: 622px; font-size: 19px; letter-spacing: 2.4px; }
  .venue-address { top: 648px; font-size: 15.5px; }
  .dress-code {
    left: 61px; top: 768px; display: flex; align-items: flex-start; gap: 12px;
  }
  .dress-code .label { font-size: 33px; font-weight: 700; line-height: 1.13; }
  .dress-code .details { font-size: 19px; line-height: 1.27; padding-top: 2px; }
  .booking { left: 536px; top: 746px; }
  .booking .rsvp { font-size: 23px; line-height: 1.25; }
  .booking .price { font-size: 32px; font-weight: 500; line-height: 1.3; }
  .booking .price strong { font-weight: 700; }
</style>
</head>
<body>
<div class="canvas">
  <section class="invitation">
    <div class="ornament-field" role="img" aria-label="Faint silver mandala scroll pattern behind the panel"></div>

    <svg class="frame-art" viewBox="0 0 908 908" aria-hidden="true">
      <g stroke="var(--frame)" stroke-width="2.5" fill="none" stroke-linecap="round">
        <path d="M31 40 V31 H420 M488 31 H875 V40" stroke-dasharray="90 8 10 8"/>
        <path d="M31 868 V877 H420 M488 877 H875 V868" stroke-dasharray="90 8 10 8"/>
        <path d="M31 48 V420 M31 488 V860" stroke-dasharray="70 8 8 8"/>
        <path d="M875 48 V420 M875 488 V860" stroke-dasharray="70 8 8 8"/>
      </g>
    </svg>

    <svg class="panel-art" viewBox="0 0 908 908" aria-hidden="true">
      <path d="M240 103 H418 Q440 103 453 78 Q466 103 488 103 H707 Q734 103 734 130 V282 Q734 298 756 312 Q734 326 734 342 V718 Q734 718 734 718 H182 V342 Q182 326 160 312 Q182 298 182 282 V130 Q182 103 209 103 Z"
            fill="var(--card)" stroke="var(--ink)" stroke-width="2"/>
      <path d="M182 586 V690 Q182 718 209 718 H418 Q440 718 453 746 Q466 718 488 718 H707 Q734 718 734 690 V586"
            fill="none" stroke="var(--ink)" stroke-width="2"/>
    </svg>

    <div class="medallion top" role="img" aria-label="Silver scroll medallion"></div>
    <div class="medallion bottom" role="img" aria-label="Silver scroll medallion"></div>
    <div class="medallion left" role="img" aria-label="Silver scroll medallion"></div>
    <div class="medallion right" role="img" aria-label="Silver scroll medallion"></div>

    <p class="host centered">Brenfield Chamber of Commerce</p>
    <h1 class="event-title centered">Copper &amp; Pearl Gala</h1>
    <div class="title-flourish" role="img" aria-label="Silver scroll divider"></div>
    <p class="invite-line">JOIN US FOR THE CELEBRATION</p>
    <p class="event-date centered">JUNE 3, 2023</p>

    <div class="schedule-band">
      <div class="slot social"><span>Social Hour</span><span>6:00 p.m.</span></div>
      <div class="slot day">SATURDAY</div>
      <div class="slot dinner"><span>Dinner</span><span>7:00 p.m.</span></div>
    </div>

    <p class="venue centered">BRENFIELD HIGH SCHOOL GYMNASIUM</p>
    <p class="venue-address centered">218 Alder Street, Brenfield, Kansas</p>

    <div class="dress-code">
      <p class="label">DRESS<br>CODE</p>
      <p class="details">Black &amp; White Attire<br>Smart Casual to<br>Fancy Formal</p>
    </div>

    <div class="booking">
      <p class="rsvp">RSVP<br>Monday, May 29, 2023</p>
      <p class="price">TICKET PRICE <strong>$30</strong></p>
    </div>
  </section>
</div>
</body>
</html>
```